Business Card- Can you make it cool vs boring!

Need a refresh on my business card! Want it to be modern but simple, classic and a pop of coolness! we do senior living and it is boring. but that doesn't mean our business card have to look boring! Open to two sided cards. our website is www.Dunmere-PK.com

Target Market(s)

capital market

Industry/Entity Type

senior housing/ real estate

Contact Information for Business Card

logo/ name/ cell/ address/ www.Dunmere-PK.com/ space for a QR code

Requirements
Must have
• maybe a QR code (do not make prominent I may not use the QR so design where it can be taken out) that link to more about us/ landing page. needs to be modern but clean
Should not have
• clip art or script

```html
<!DOCTYPE html>
<html lang="en">
<head>
<meta charset="utf-8">
<title>Dunmere Living – Business Card</title>
<link href="https://fonts.googleapis.com/css2?family=Poppins:wght@400;600;700&display=swap" rel="stylesheet">
<style>
  :root {
    --orange: #e2712b;
    --orange-soft: #e98a4c;
    --black: #000000;
    --white: #ffffff;
    --ink: #1c1c1c;
    --stage: #e6e6e6;
    --photo-dark: #3a3a3a;
    --photo-mid: #6e6e6e;
  }
  * { box-sizing: border-box; margin: 0; padding: 0; }
  html, body {
    width: 1092px; height: 1200px; overflow: hidden;
    background: var(--stage);
    font-family: "Poppins", sans-serif;
  }
  .card {
    position: absolute; left: 153px; width: 787px; height: 450px;
    overflow: hidden; box-shadow: 0 10px 30px rgba(0,0,0,.22);
  }
  .card--front { top: 104px; background: var(--black); }
  .card--back { top: 646px; background: var(--white); }

  /* front */
  .front__band {
    position: absolute; left: 0; top: 0; width: 100%; height: 186px;
    background: linear-gradient(90deg, var(--orange-soft), var(--orange) 55%, var(--orange-soft));
  }
  .hex { position: absolute; }
  .front__hex { left: 250px; top: 34px; width: 286px; height: 320px; }
  .back__hex { left: 400px; top: 105px; width: 221px; height: 244px; }
  .hex svg { position: absolute; inset: 0; width: 100%; height: 100%; overflow: visible; }
  .brand {
    position: absolute; left: 0; right: 0; text-align: center;
    color: var(--orange); font-weight: 600; white-space: nowrap;
  }
  .front__hex .brand { top: 142px; font-size: 27px; }
  .back__hex .brand { top: 106px; font-size: 21px; }

  .front__tab { position: absolute; left: 80px; top: 386px; width: 617px; height: 64px; }
  .front__url {
    position: absolute; left: 0; right: 0; top: 394px; text-align: center;
    font-size: 33px; letter-spacing: 3px; color: var(--ink);
  }
  .front__url b { color: var(--orange); font-weight: 700; }

  /* back */
  .back__stripe { position: absolute; left: 494px; top: 0; width: 44px; height: 100%; background: var(--orange); }
  .back__photo {
    position: absolute; left: 538px; top: 0; width: 249px; height: 100%;
    background: linear-gradient(160deg, var(--photo-mid), var(--photo-dark));
  }
  .person__name {
    position: absolute; left: 50px; top: 38px;
    font-size: 40px; font-weight: 700; letter-spacing: 3px; color: var(--orange);
  }
  .person__role {
    position: absolute; left: 50px; top: 90px;
    font-size: 31px; letter-spacing: 2.5px; color: var(--ink);
  }
  .person__rule { position: absolute; left: 50px; top: 140px; width: 193px; height: 1.5px; background: var(--ink); }

  .contact { position: absolute; left: 51px; display: flex; align-items: flex-start; gap: 13px; }
  .contact__icon { width: 36px; height: 36px; flex: none; }
  .contact__text { font-size: 24px; letter-spacing: 2.6px; line-height: 30px; color: var(--ink); padding-top: 2px; }
  .contact--phone { top: 214px; }
  .contact--address { top: 281px; }
  .contact--web { top: 363px; }
  .contact--web .contact__text { letter-spacing: 0.5px; }
</style>
</head>
<body>

<section class="card card--front">
  <div class="front__band" role="img" aria-label="Photo of a senior resident with a caregiver, tinted orange"></div>
  <div class="hex front__hex">
    <svg viewBox="0 0 286 320">
      <polygon points="143,12 272,86 272,234 143,308 14,234 14,86" fill="#e2712b" stroke="#e2712b" stroke-width="24" stroke-linejoin="round"/>
      <polygon points="143,36 250,98 250,222 143,284 36,222 36,98" fill="#fff" stroke="#fff" stroke-width="16" stroke-linejoin="round"/>
    </svg>
    <div class="brand">Dunmere Living</div>
  </div>
  <svg class="front__tab" viewBox="0 0 617 64" preserveAspectRatio="none">
    <path d="M0,64 L38,16 Q52,0 78,0 L539,0 Q565,0 579,16 L617,64 Z" fill="#fff"/>
  </svg>
  <div class="front__url">www.<b>Dunmere-PK</b>.com</div>
</section>

<section class="card card--back">
  <div class="back__stripe"></div>
  <div class="back__photo" role="img" aria-label="Black and white photo of a caregiver talking with an elderly resident"></div>
  <div class="hex back__hex">
    <svg viewBox="0 0 221 244">
      <polygon points="110.5,10 210,66 210,178 110.5,234 11,178 11,66" fill="#e2712b" stroke="#e2712b" stroke-width="20" stroke-linejoin="round"/>
      <polygon points="110.5,28 194,76 194,168 110.5,216 27,168 27,76" fill="#fff" stroke="#fff" stroke-width="14" stroke-linejoin="round"/>
    </svg>
    <div class="brand">Dunmere Living</div>
  </div>

  <h1 class="person__name">Clara Hensley</h1>
  <p class="person__role">senior living</p>
  <div class="person__rule"></div>

  <div class="contact contact--phone">
    <svg class="contact__icon" viewBox="0 0 36 36" aria-hidden="true">
      <circle cx="18" cy="18" r="18" fill="#e2712b"/>
      <path d="M12 9 l4 0 l1.5 5 l-2.5 2 q2 4 5 5 l2-2.5 l5 1.5 l0 4 q-1 2-3 2 q-9-1-14-10 q-1-4 2-7 z" fill="none" stroke="#fff" stroke-width="2" stroke-linejoin="round"/>
    </svg>
    <span class="contact__text">(555) 204-7316</span>
  </div>

  <div class="contact contact--address">
    <svg class="contact__icon" viewBox="0 0 36 36" aria-hidden="true">
      <circle cx="18" cy="18" r="18" fill="#e2712b"/>
      <path d="M18 26 q-7-7-7-11 a7 7 0 0 1 14 0 q0 4-7 11 z" fill="none" stroke="#fff" stroke-width="2"/>
      <circle cx="18" cy="15" r="2.5" fill="#fff"/>
      <path d="M11 28 h14" stroke="#fff" stroke-width="2"/>
    </svg>
    <span class="contact__text">418 Larkfield Lane,<br>Suite #604</span>
  </div>

  <div class="contact contact--web">
    <svg class="contact__icon" viewBox="0 0 36 36" aria-hidden="true">
      <circle cx="18" cy="18" r="18" fill="#e2712b"/>
      <g fill="none" stroke="#fff" stroke-width="1.8">
        <circle cx="18" cy="18" r="9"/>
        <ellipse cx="18" cy="18" rx="4" ry="9"/>
        <path d="M9 18 h18 M10.5 13 h15 M10.5 23 h15"/>
      </g>
    </svg>
    <span class="contact__text">www.Dunmere-PK.com</span>
  </div>
</section>

</body>
</html>
```